Velk Partners Building Business Cards

We need a business card that reflects our business as "Solar Experts" in San Diego. Browse our website www.velkpartners.example our License needs to be displayed as "CSLB# 3867140" our phone number is (619) 555-0187

Save thousands on your electric bills and increase the value of your home while helping to protect the environment. Our solar installation experts will help you design the system that's right for you, using only the highest quality equipment that will look great and give you ideal performance. Our goal is to make you energy independent, and get your electric bill to 0.

Paul Osterby
(619) 555-0187
paul@velkpartners.example

Target Market(s)

Home owners in san diego looking for solar

Industry/Entity Type

Solar Energy

Contact Information for Business Card

Paul Osterby
(619) 555-0187
paul@velkpartners.example

Font styles to use
Other font styles liked:
• Use our logo font

Requirements
Must have
• License needs to be displayed as "CSLB# 3867140" our phone number is (619) 555-0187
Nice to have
• Real images of rooftop home solar in san diego
Should not have
• our business address

```html
<!DOCTYPE html>
<html lang="en">
<head>
<meta charset="utf-8">
<title>Velk Partners Building – Business Cards</title>
<link href="https://fonts.googleapis.com/css2?family=Roboto:wght@400;500;700&display=swap" rel="stylesheet">
<style>
  :root {
    --bg: #a9a7a8;
    --navy: #2b4a96;
    --navy-deep: #213d80;
    --ink: #233f7d;
    --gold: #eca717;
    --white: #ffffff;
    --text: #1f3a78;
  }
  * { margin: 0; padding: 0; box-sizing: border-box; }
  html, body {
    width: 1200px; height: 1200px; overflow: hidden;
    background: var(--bg);
    font-family: "Roboto", Arial, sans-serif;
  }
  .card {
    position: absolute;
    width: 710px;
    height: 418px;
    border-radius: 22px;
    overflow: hidden;
  }
  /* Front */
  .card-front { top: 118px; left: 240px; background: var(--navy); }
  .front-backdrop {
    position: absolute; inset: 0;
    background: linear-gradient(160deg, #3352a3 0%, var(--navy) 50%, var(--navy-deep) 100%);
  }
  .brand-name {
    position: absolute; left: 0; right: 0; top: 140px;
    text-align: center;
    color: var(--white);
    font-weight: 700;
    font-size: 50px;
    line-height: 1.1;
    letter-spacing: -0.5px;
  }
  .front-license {
    position: absolute; left: 0; right: 0; top: 364px;
    display: flex; justify-content: center; align-items: center; gap: 20px;
    color: var(--white);
    font-size: 17px;
  }
  .front-license .rule { width: 55px; height: 3px; background: var(--gold); }

  /* Back */
  .card-back { top: 645px; left: 232px; background: var(--white); }
  .back-brand {
    position: absolute; left: 62px; top: 150px; width: 270px;
    display: flex; align-items: center; gap: 16px;
  }
  .back-brand .dot { flex: none; width: 46px; height: 46px; border-radius: 50%; background: var(--gold); }
  .back-brand .name {
    color: var(--ink); font-weight: 700; font-size: 27px; line-height: 1.15;
  }
  .contact {
    position: absolute; left: 388px; top: 112px;
    color: var(--text);
  }
  .contact .person { font-size: 24px; font-weight: 700; color: var(--ink); }
  .contact .role { font-size: 16px; margin-top: 4px; }
  .contact ul { list-style: none; margin-top: 30px; }
  .contact li { display: flex; align-items: center; gap: 14px; font-size: 18px; height: 25px; white-space: nowrap; }
  .contact li svg { width: 20px; height: 16px; fill: var(--gold); flex: none; }
  .contact .accent { color: var(--gold); }
  .contact .license { font-size: 18px; margin-top: 7px; }
</style>
</head>
<body>
  <section class="card card-front">
    <div class="front-backdrop" role="img" aria-label="Rooftop solar panel array, tinted blue"></div>
    <div class="brand-name">Velk Partners<br>Building Inc</div>
    <div class="front-license"><span class="rule"></span><span>License: CSLB# 3867140</span><span class="rule"></span></div>
  </section>

  <section class="card card-back">
    <div class="back-brand">
      <span class="dot"></span>
      <span class="name">Velk Partners Building</span>
    </div>
    <div class="contact">
      <div class="person">Paul Osterby</div>
      <div class="role">Managing Director</div>
      <ul>
        <li><svg viewBox="0 0 20 16" aria-hidden="true"><path d="M2 5c0-2 3-3 8-3s8 1 8 3v2h-4V5H6v2H2zM5 8h10l2 7H3z"/></svg><span class="value">(619) 555-0187</span></li>
        <li><svg viewBox="0 0 20 16" aria-hidden="true"><path d="M1 2h18v12H1zm2 2v.5l7 5 7-5V4l-7 5z"/></svg><span class="value">paul@velkpartners.example</span></li>
        <li><svg viewBox="0 0 20 16" aria-hidden="true"><circle cx="10" cy="8" r="7" fill="none" stroke="#eca717" stroke-width="1.6"/><path d="M3 8h14M10 1c-3 4-3 10 0 14M10 1c3 4 3 10 0 14" fill="none" stroke="#eca717" stroke-width="1.4"/></svg><span class="value">www.<span class="accent">velkpartners</span>.example</span></li>
      </ul>
      <div class="license">License: CSLB# 3867140</div>
    </div>
  </section>
</body>
</html>
```